Tidewell-Network Theme For Forums!

We are looking for a theme for our forums. The forums are ran off Invision Power Boards. We have a basic theme on there now but we want more our own feel. If possible have some longboarding accept incorporated in the theme. We want the theme to have some red in it to match our logo. Tidewell-network.com

Target Market(s)

Skatingboarding & Longboarding

Coding

Coded - Design and coding required

Number of Pages Required

1 page

Colors
f04a50

```html
<!DOCTYPE html>
<html lang="en">
<head>
<meta charset="utf-8">
<title>Tidewell-Network Forums</title>
<link href="https://fonts.googleapis.com/css2?family=Open+Sans:wght@400;600;700&display=swap" rel="stylesheet">
<style>
:root{
  --red:#e03c4a;
  --red-dark:#c9303d;
  --pink:#f0cbcf;
  --page:#f4f4f4;
  --side:#ebebeb;
  --cell-a:#eeeeee;
  --cell-b:#e4e4e4;
  --ink:#1e1e1e;
  --muted:#333;
  --white:#fff;
}
*{box-sizing:border-box;margin:0;padding:0}
html,body{width:1200px;height:954px;overflow:hidden}
body{font-family:"Open Sans",Arial,sans-serif;background:var(--page);color:var(--ink);position:relative}
.site-header{height:80px;position:relative}
.brand{position:absolute;left:26px;top:26px;display:flex;align-items:center;gap:8px;font-size:24px;font-weight:700;color:var(--red);letter-spacing:.5px}
.brand-dot{width:14px;height:14px;border-radius:50%;background:var(--red)}
.member-login{position:absolute;right:42px;top:23px;display:flex;align-items:center;gap:10px;font-size:12.5px;font-weight:600;letter-spacing:.4px;color:#333}
.member-login .lock{width:33px;height:33px;border-radius:50%;background:#dcdcdc;display:flex;align-items:center;justify-content:center}
.main-nav{position:absolute;top:80px;left:0;width:1200px;height:37px;background:linear-gradient(#e34553,#d8384a);display:flex;align-items:center}
.main-nav ul{list-style:none;display:flex;margin-left:49px}
.main-nav li{color:var(--white);font-size:12.5px;margin-right:28px;display:flex;align-items:center;gap:6px}
.badge{width:15px;height:15px;border-radius:50%;background:var(--white);color:var(--ink);font-size:9px;font-weight:700;display:inline-flex;align-items:center;justify-content:center}
.search{position:absolute;left:950px;top:5px;width:203px;height:21px;background:var(--white);font-size:10.5px;color:#555;padding:3px 10px;display:flex;justify-content:space-between;align-items:center}
.gear{position:absolute;left:1169px;top:11px}
.sidebar-bg{position:absolute;left:911px;top:117px;width:289px;height:799px;background:var(--side)}
.actions{position:absolute;top:140px;left:639px;display:flex;gap:8px}
.btn{height:27px;display:flex;align-items:center;gap:7px;padding:0 12px;color:var(--white);font-size:11px}
.btn-watch{background:var(--red);width:107px}
.btn-start{background:#111;width:125px}
.forum{position:absolute;left:26px;width:853px}
.forum-title{height:36px;background:var(--red);color:var(--white);font-weight:600;font-size:14px;padding:9px 15px}
.forum-sub{height:31px;background:var(--pink);font-size:12px;font-weight:600;padding:6px 14px}
.row{display:grid;grid-template-columns:38px 318px 123px 126px 205px 43px;height:61px;border-bottom:1px solid #f7f7f7}
.row.head{height:32px;background:#f1f1f1;border:0}
.head div{color:var(--red);font-weight:600;font-size:12px;display:flex;align-items:center}
.c-icon{background:var(--cell-b);display:flex;align-items:center;justify-content:center}
.c-topic{background:var(--cell-a);display:flex;align-items:center;gap:9px;padding-left:13px}
.c-topic strong{display:block;font-weight:400;font-size:12.5px}
.c-topic span{font-size:10px}
.c-start{background:var(--cell-b);display:flex;align-items:center;justify-content:center;gap:6px;font-size:10px}
.c-stats{background:var(--cell-a);text-align:center;font-size:10px;padding-top:12px;line-height:20px}
.c-stats b{font-weight:600}
.c-last{background:var(--cell-b);font-size:10px;padding:12px 0 0 16px;line-height:20px}
.c-last b{font-weight:600}
.c-last span{padding-left:10px}
.c-check{background:#f0f0f0;display:flex;align-items:center;justify-content:center}
.box{width:12px;height:12px;border:1px solid #cfcfcf;background:#f6f6f6}
.head .c-check{background:none}
.panel{position:absolute;left:930px;width:251px;background:var(--white)}
.panel-head{height:36px;background:var(--red);color:var(--white);font-weight:600;font-size:12.5px;display:flex;align-items:center;padding-left:14px;gap:10px;position:relative}
.panel-head .toggle{position:absolute;right:0;top:0;width:28px;height:36px;background:var(--red-dark);display:flex;align-items:center;justify-content:center;font-size:14px}
.mind{margin:11px 0 0 25px;width:203px;height:22px;background:#f1f1f1;font-size:10.5px;padding:3px 10px;position:relative}
.mind .go{position:absolute;right:0;top:0;width:31px;height:22px;background:#f6cdd0;display:flex;align-items:center;justify-content:center}
.status{display:flex;gap:8px;margin:0 10px 0 12px;padding:14px 0 8px;border-bottom:1px solid #e6e6e6;font-size:10px;line-height:15px}
.status:last-child{border:0}
.avatar{flex:0 0 51px;height:51px;background:linear-gradient(#8a5a3e,#3d2a22)}
.status .lead{color:var(--red);font-weight:600}
.status .meta{font-weight:700;font-size:8.5px;line-height:13px}
.status .tools{font-size:8.5px;color:#444}
.recent{margin:0 10px;padding:14px 4px 11px;border-bottom:1px solid #e6e6e6}
.recent:last-child{border:0}
.recent strong{font-size:12px;font-weight:700;display:flex;align-items:center;gap:6px}
.recent span{font-size:9.5px;display:block;margin-top:4px}
.site-footer{position:absolute;top:916px;left:0;width:1200px;height:38px;background:var(--white);text-align:center;font-size:11.5px;padding-top:16px}
</style>
</head>
<body>
<svg width="0" height="0" style="position:absolute">
  <defs>
    <symbol id="board" viewBox="0 0 30 30"><g fill="none" stroke="#e03c4a" stroke-width="1.6"><rect x="2" y="11" width="26" height="8" rx="4" transform="rotate(-45 15 15)"/><circle cx="8" cy="16" r="1.5"/><circle cx="16" cy="8" r="1.5"/><circle cx="14" cy="22" r="1.5"/><circle cx="22" cy="14" r="1.5"/></g></symbol>
    <symbol id="deck" viewBox="0 0 30 20"><g fill="none" stroke="#e03c4a" stroke-width="1.5"><path d="M6 5h20a3 3 0 0 1 0 8H6"/><path d="M2 13h26"/><circle cx="9" cy="16" r="2.3"/><circle cx="23" cy="16" r="2.3"/><path d="M1 7h4M2 10h3"/></g></symbol>
    <symbol id="mark-full" viewBox="0 0 10 13"><path d="M1 1h8v11L5 9 1 12z" fill="#e03c4a"/></symbol>
    <symbol id="mark-open" viewBox="0 0 10 13"><path d="M1 1h8v11L5 9 1 12z" fill="none" stroke="#e03c4a" stroke-width="1.4"/></symbol>
    <symbol id="ext" viewBox="0 0 10 10"><g fill="none" stroke="#222" stroke-width="1.4"><path d="M7 5.5V9H1V3h3.5"/><path d="M5 5l4-4M6 1h3v3"/></g></symbol>
  </defs>
</svg>

<header class="site-header">
  <div class="brand"><span class="brand-dot"></span>Tidewell-Network</div>
  <div class="member-login"><span class="lock"><svg width="11" height="13" viewBox="0 0 11 13"><rect x="1" y="5.5" width="9" height="7" fill="#fff"/><path d="M3 6V4a2.5 2.5 0 0 1 5 0v2" fill="none" stroke="#fff" stroke-width="1.6"/></svg></span>MEMBER LOGIN</div>
</header>

<nav class="main-nav">
  <ul><li>Forums</li><li>Members</li><li>Calendar</li><li>Blogs</li><li>Gallery</li><li>Longboards</li><li>Chat <span class="badge">0</span></li></ul>
  <div class="search">Search <svg width="11" height="11" viewBox="0 0 11 11"><circle cx="4.5" cy="4.5" r="3.5" fill="none" stroke="#222" stroke-width="1.6"/><path d="M7 7l3 3" stroke="#222" stroke-width="1.8"/></svg></div>
  <svg class="gear" width="12" height="12" viewBox="0 0 12 12"><g fill="#fff"><circle cx="6" cy="6" r="3.6"/><rect x="5" y="0" width="2" height="12"/><rect x="0" y="5" width="12" height="2"/><rect x="5" y="0" width="2" height="12" transform="rotate(45 6 6)"/><rect x="5" y="0" width="2" height="12" transform="rotate(-45 6 6)"/></g><circle cx="6" cy="6" r="1.5" fill="#d8384a"/></svg>
</nav>

<div class="sidebar-bg"></div>

<div class="actions">
  <div class="btn btn-watch"><svg width="12" height="8" viewBox="0 0 12 8"><path d="M0 4q6-8 12 0-6 8-12 0z" fill="#fff"/><circle cx="6" cy="4" r="1.8" fill="#e03c4a"/></svg>Watch Forum</div>
  <div class="btn btn-start"><svg width="9" height="11" viewBox="0 0 9 11"><path d="M0 0h6l3 3v8H0z" fill="#fff"/><path d="M2 5h5M2 7h5" stroke="#111"/></svg>Start New Topics</div>
</div>

<section class="forum" style="top:182px">
  <div class="forum-title">Finibus Bonorum et Malorum</div>
  <div class="forum-sub">Longboard Statistics discussion</div>
  <div class="row head"><div></div><div style="padding-left:21px">Topic</div><div style="padding-left:30px">Started By</div><div style="padding-left:22px">Stats</div><div style="padding-left:15px">Last Post Info</div><div class="c-check"><span class="box"></span></div></div>
  <div class="row"><div class="c-icon"><svg width="26" height="26"><use href="#board"/></svg></div><div class="c-topic"><svg width="10" height="13"><use href="#mark-full"/></svg><div><strong>Sed ut perspiciatis unde omnis iste natus</strong><span>a guide with Pictures</span></div></div><div class="c-start">John 435 <svg width="9" height="9"><use href="#ext"/></svg></div><div class="c-stats"><b>1 Reply</b><br>105 Views</div><div class="c-last"><b>Today 01:05 PM</b><br><span>By : Smith</span></div><div class="c-check"><span class="box"></span></div></div>
  <div class="row"><div class="c-icon"><svg width="26" height="26"><use href="#board"/></svg></div><div class="c-topic"><svg width="10" height="13"><use href="#mark-open"/></svg><div><strong>Sed ut perspiciatis unde omnis iste natus</strong><span>a guide with Pictures</span></div></div><div class="c-start">John 435 <svg width="9" height="9"><use href="#ext"/></svg></div><div class="c-stats"><b>1 Reply</b><br>105 Views</div><div class="c-last"><b>Today 01:05 PM</b><br><span>By : Smith</span></div><div class="c-check"><span class="box"></span></div></div>
  <div class="row"><div class="c-icon"><svg width="26" height="26"><use href="#board"/></svg></div><div class="c-topic"><svg width="10" height="13"><use href="#mark-full"/></svg><div><strong>Sed ut perspiciatis unde omnis iste natus</strong><span>a guide with Pictures</span></div></div><div class="c-start">John 435 <svg width="9" height="9"><use href="#ext"/></svg></div><div class="c-stats"><b>1 Reply</b><br>105 Views</div><div class="c-last"><b>Today 01:05 PM</b><br><span>By : Smith</span></div><div class="c-check"><span class="box"></span></div></div>
  <div class="row"><div class="c-icon"><svg width="26" height="26"><use href="#board"/></svg></div><div class="c-topic"><svg width="10" height="13"><use href="#mark-open"/></svg><div><strong>Sed ut perspiciatis unde omnis iste natus</strong><span>a guide with Pictures</span></div></div><div class="c-start">John 435 <svg width="9" height="9"><use href="#ext"/></svg></div><div class="c-stats"><b>1 Reply</b><br>105 Views</div><div class="c-last"><b>Today 01:05 PM</b><br><span>By : Smith</span></div><div class="c-check"><span class="box"></span></div></div>
</section>

<section class="forum" style="top:543px">
  <div class="forum-title">Finibus Bonorum et Malorum</div>
  <div class="forum-sub">Sakateboard views discussion</div>
  <div class="row head"><div></div><div style="padding-left:21px">Topic</div><div style="padding-left:30px">Started By</div><div style="padding-left:22px">Stats</div><div style="padding-left:15px">Last Post Info</div><div class="c-check"><span class="box"></span></div></div>
  <div class="row"><div class="c-icon"><svg width="28" height="19"><use href="#deck"/></svg></div><div class="c-topic"><svg width="10" height="13"><use href="#mark-open"/></svg><div><strong>Sed ut perspiciatis unde omnis iste natus</strong><span>a guide with Pictures</span></div></div><div class="c-start">John 435 <svg width="9" height="9"><use href="#ext"/></svg></div><div class="c-stats"><b>1 Reply</b><br>105 Views</div><div class="c-last"><b>Today 01:05 PM</b><br><span>By : Smith</span></div><div class="c-check"><span class="box"></span></div></div>
  <div class="row"><div class="c-icon"><svg width="28" height="19"><use href="#deck"/></svg></div><div class="c-topic"><svg width="10" height="13"><use href="#mark-full"/></svg><div><strong>Sed ut perspiciatis unde omnis iste natus</strong><span>a guide with Pictures</span></div></div><div class="c-start">John 435 <svg width="9" height="9"><use href="#ext"/></svg></div><div class="c-stats"><b>1 Reply</b><br>105 Views</div><div class="c-last"><b>Today 01:05 PM</b><br><span>By : Smith</span></div><div class="c-check"><span class="box"></span></div></div>
  <div class="row"><div class="c-icon"><svg width="28" height="19"><use href="#deck"/></svg></div><div class="c-topic"><svg width="10" height="13"><use href="#mark-open"/></svg><div><strong>Sed ut perspiciatis unde omnis iste natus</strong><span>a guide with Pictures</span></div></div><div class="c-start">John 435 <svg width="9" height="9"><use href="#ext"/></svg></div><div class="c-stats"><b>1 Reply</b><br>105 Views</div><div class="c-last"><b>Today 01:05 PM</b><br><span>By : Smith</span></div><div class="c-check"><span class="box"></span></div></div>
  <div class="row"><div class="c-icon"><svg width="28" height="19"><use href="#deck"/></svg></div><div class="c-topic"><svg width="10" height="13"><use href="#mark-full"/></svg><div><strong>Sed ut perspiciatis unde omnis iste natus</strong><span>a guide with Pictures</span></div></div><div class="c-start">John 435 <svg width="9" height="9"><use href="#ext"/></svg></div><div class="c-stats"><b>1 Reply</b><br>105 Views</div><div class="c-last"><b>Today 01:05 PM</b><br><span>By : Smith</span></div><div class="c-check"><span class="box"></span></div></div>
</section>

<aside class="panel" style="top:131px;height:242px">
  <div class="panel-head"><svg width="11" height="11" viewBox="0 0 11 11"><circle cx="5.5" cy="3" r="2.8" fill="#fff"/><path d="M0 11q0-5 5.5-5t5.5 5z" fill="#fff"/></svg>Recent Status Updates<span class="toggle">–</span></div>
  <div class="mind">What's on your Mind ?<span class="go"><svg width="10" height="10" viewBox="0 0 10 10"><path d="M0 5h8M5 1.5 8.5 5 5 8.5" fill="none" stroke="#e03c4a" stroke-width="1.6"/></svg></span></div>
  <div class="status"><div class="avatar" role="img" aria-label="Member profile photo"></div><div><span class="lead">Ut enim ad minima</span> veniam, quis nostrum exercitationem ullam.<div class="meta">May 07 2018 &nbsp;05:03 PM via Chirper</div><div class="tools">Delete &nbsp;. Lock &nbsp;. Add Comment</div></div></div>
  <div class="status"><div class="avatar" role="img" aria-label="Member profile photo"></div><div><span class="lead">Ut enim ad minima</span> veniam, quis nostrum exercitationem ullam.<div class="meta">May 07 2018 &nbsp;05:03 PM via Chirper</div><div class="tools">Delete &nbsp;. Lock &nbsp;. Add Comment</div></div></div>
</aside>

<aside class="panel" style="top:386px;height:168px">
  <div class="panel-head"><svg width="9" height="11" viewBox="0 0 9 11"><path d="M0 0h6l3 3v8H0z" fill="#fff"/><path d="M2 5h5M2 7h5" stroke="#e03c4a"/></svg>Recently Added Topics<span class="toggle">–</span></div>
  <div class="recent"><strong>Skateboard by John <svg width="9" height="9"><use href="#ext"/></svg></strong><span>Feb 05 2018 05 :04PM</span></div>
  <div class="recent"><strong>Longboard by Smith <svg width="9" height="9"><use href="#ext"/></svg></strong><span>Feb 05 2018 05 :04PM</span></div>
</aside>

<footer class="site-footer">2018 © &nbsp;| &nbsp;www.tidewell-network.com</footer>
</body>
</html>
```